Corvane Capital Business Cards

These are professional business cards that are for my family office.
Put fake emails and phone numbers as of now until I finalize those components. This family office controls my families investments, assets, and future. The cards should be professional.
..
.
.
.
I just uploaded another variation of a logo I would like to see as a business card to I am inbeteen which logo to use

Target Market(s)

business

Industry/Entity Type

business

Contact Information for Business Card

Professional, wealth related, finance related.

Requirements
Must have
• Logo

```html
<!DOCTYPE html>
<html lang="en">
<head>
<meta charset="UTF-8">
<title>Corvane Capital Business Cards</title>
<link href="https://fonts.googleapis.com/css2?family=Cinzel:wght@500;600&family=Montserrat:wght@400;500&display=swap" rel="stylesheet">
<style>
  :root {
    --navy: #1a1f2c;
    --white: #ffffff;
    --stage: #d2d2d2;
    --muted: #3a3f4c;
    --rule: #c4c6cc;
  }
  * { margin: 0; padding: 0; box-sizing: border-box; }
  html, body { width: 1200px; height: 802px; overflow: hidden; }
  body {
    background: var(--stage);
    display: flex;
    align-items: center;
    justify-content: center;
    gap: 40px;
    font-family: "Montserrat", sans-serif;
  }
  .card {
    width: 540px;
    height: 310px;
    border-radius: 22px;
    position: relative;
    overflow: hidden;
    box-shadow: 0 10px 28px rgba(0,0,0,0.22);
  }
  .card--front { background: var(--white); color: var(--navy); }
  .card--back { background: var(--navy); color: var(--white); display: flex; align-items: center; justify-content: center; }

  .brand {
    display: flex;
    align-items: center;
    gap: 12px;
    font-family: "Cinzel", serif;
    font-weight: 600;
    letter-spacing: 0.04em;
  }
  .brand__dot {
    border-radius: 50%;
    border: 2px solid currentColor;
    flex: none;
  }
  .card--front .brand { position: absolute; top: 38px; left: 0; right: 0; justify-content: center; font-size: 24px; }
  .card--front .brand__dot { width: 16px; height: 16px; }
  .card--back .brand { font-size: 38px; }
  .card--back .brand__dot { width: 26px; height: 26px; }

  .details {
    position: absolute;
    top: 108px;
    left: 0; right: 0;
    display: flex;
    justify-content: center;
    align-items: center;
    gap: 26px;
  }
  .person { text-align: right; }
  .person__name { font-family: "Cinzel", serif; font-weight: 500; font-size: 22px; letter-spacing: 0.03em; }
  .person__title { font-size: 14px; color: var(--muted); margin-top: 2px; }
  .divider { width: 1px; height: 70px; background: var(--rule); }
  .contact { list-style: none; font-size: 14px; line-height: 1.75; color: var(--muted); }
  .contact li { display: flex; align-items: center; gap: 8px; }
  .contact svg { width: 12px; height: 12px; fill: var(--navy); flex: none; }

  .address-band {
    position: absolute;
    left: 0; right: 0;
    top: 220px;
    height: 36px;
    background: var(--navy);
    color: var(--white);
    font-size: 14.5px;
    letter-spacing: 0.02em;
    display: flex;
    align-items: center;
    justify-content: center;
  }
</style>
</head>
<body>
  <section class="card card--front" aria-label="Business card front">
    <div class="brand"><span class="brand__dot"></span>Corvane Capital</div>
    <div class="details">
      <div class="person">
        <p class="person__name">Elias Moreno</p>
        <p class="person__title">CEO/Founder</p>
      </div>
      <span class="divider"></span>
      <ul class="contact">
        <li><svg viewBox="0 0 12 12"><path d="M2.5 1h2l1 2.6-1.3 1A6 6 0 0 0 7.4 7.8l1-1.3L11 7.5v2A1.5 1.5 0 0 1 9.5 11 8.5 8.5 0 0 1 1 2.5 1.5 1.5 0 0 1 2.5 1z"/></svg>(555) 318-4476</li>
        <li><svg viewBox="0 0 12 12"><path d="M1 3h10v6.5H1z M1.4 3.2 6 6.8l4.6-3.6" stroke="#fff" stroke-width="0.8"/></svg>EliasM@corvanecapital.com</li>
        <li><svg viewBox="0 0 12 12"><circle cx="6" cy="6" r="5"/><path d="M1 6h10M6 1c-2.2 2.8-2.2 7.2 0 10M6 1c2.2 2.8 2.2 7.2 0 10" stroke="#fff" stroke-width="0.7" fill="none"/></svg>www.corvanecapital.com</li>
      </ul>
    </div>
    <div class="address-band">4870 Larkspur Ave Suite 210 Halden, AB 604215</div>
  </section>

  <section class="card card--back" aria-label="Business card back">
    <div class="brand"><span class="brand__dot"></span>Corvane Capital</div>
  </section>
</body>
</html>
```